SOLVE Study flyer

I need help designing a flyer for a research study that will include brain imaging in adolescents. The info is in the attached document. The study is called the Sequoia Outlook Lantern Valley Echo (SOLVE) study. Ideally this would be returned as a document that I can edit in the future as we will have several new recruitment phases (different age groups, etc. I also would love to have a logo designed as part of this project, but I recognize that might be a separate design request.

```html
<!DOCTYPE html>
<html lang="en">
<head>
<meta charset="utf-8">
<title>SOLVE Study Flyer</title>
<link href="https://fonts.googleapis.com/css2?family=Bebas+Neue&family=Poppins:wght@400;500;600;700&family=Montserrat:wght@400;500&display=swap" rel="stylesheet">
<style>
:root{
  --navy:#141a4a;
  --navy-deep:#0f1238;
  --indigo:#2a2f86;
  --cyan:#18a9ee;
  --sky:#4fc3f7;
  --violet:#a67fd0;
  --lavender:#7a6fb4;
  --panel-blue:#4ea3d3;
  --white:#ffffff;
  --ink:#1b1f4f;
  --page:#f1f1f1;
}
*{margin:0;padding:0;box-sizing:border-box}
html,body{width:1200px;height:2281px;overflow:hidden;background:var(--page)}
body{font-family:"Poppins",sans-serif;position:relative}
.flyer{position:absolute;left:0;top:292px;width:1200px;height:1697px;overflow:hidden;
  background:linear-gradient(160deg,var(--navy-deep) 0%,var(--navy) 35%,var(--indigo) 65%,#3a3fa8 100%);
  box-shadow:0 10px 40px rgba(0,0,0,.15)}
.hero-photo{position:absolute;left:600px;top:0;width:600px;height:880px;
  background:radial-gradient(ellipse at 62% 38%,rgba(120,110,235,.9) 0%,rgba(70,70,200,.65) 35%,rgba(30,35,110,0) 72%)}
.white-base{position:absolute;left:0;top:0;width:1200px;height:1697px}
.brand{position:absolute;left:73px;top:80px;display:flex;align-items:center;gap:22px}
.brand-dot{width:70px;height:70px;border-radius:50%;background:var(--lavender)}
.brand-name{font-family:"Montserrat",sans-serif;font-weight:500;color:var(--white);font-size:56px;letter-spacing:12px;line-height:1}
.brand-tagline{position:absolute;left:165px;top:186px;font-family:"Montserrat",sans-serif;color:var(--cyan);font-size:19px;letter-spacing:1.5px;line-height:1.3;width:340px}
.headline{position:absolute;left:73px;top:320px;font-family:"Bebas Neue",sans-serif;line-height:.98}
.headline .ask{color:var(--cyan);font-size:92px;display:block;letter-spacing:1px}
.headline .sub{color:var(--violet);font-size:66px;display:block;letter-spacing:.5px}
.accent-bar{position:absolute;left:73px;top:636px;width:370px;height:4px;background:var(--cyan)}
.intro{position:absolute;left:73px;top:660px;width:1000px;color:var(--white);font-size:25px;line-height:1.45}
.intro strong{font-weight:700}
.involves{position:absolute;left:73px;top:810px;width:1058px;height:306px;border-radius:16px;
  background:linear-gradient(180deg,var(--lavender) 0%,#5f92cc 60%,var(--panel-blue) 100%);
  display:flex;padding:50px 40px 0 58px;color:var(--white)}
.involves-rule{position:absolute;left:128px;top:809px;width:940px;height:2px;background:rgba(255,255,255,.5)}
.involves-label{position:absolute;left:395px;top:786px;width:405px;height:36px;border-radius:18px;background:var(--cyan);
  color:var(--white);font-weight:600;font-size:23px;text-align:center;line-height:36px}
.step{display:flex;flex-direction:column;padding-right:18px}
.step + .step{border-left:1px solid rgba(255,255,255,.35);padding-left:18px}
.step svg{height:90px;margin-bottom:22px}
.step h3{font-size:20px;font-weight:700;line-height:1.05;text-transform:uppercase}
.step p{font-size:20px;line-height:1.2;font-weight:400}
.step-interview{width:270px}
.step-forms{width:232px}
.step-visit{width:470px}
.eligible{position:absolute;left:73px;top:1161px;width:513px;height:276px;border-radius:16px;background:var(--navy);color:var(--white);padding:26px 26px}
.eligible-head{display:flex;align-items:center;gap:14px;font-weight:700;font-size:20px;line-height:1.05;text-transform:uppercase;padding-bottom:10px;border-bottom:1px solid rgba(255,255,255,.5);width:280px}
.eligible ul{list-style:none;margin-top:18px}
.eligible li{display:flex;gap:16px;font-size:20px;line-height:1.25;margin-bottom:12px}
.eligible li svg{flex:none;margin-top:3px}
.comp{position:absolute;left:612px;top:1161px;width:516px;height:276px;border-radius:16px;
  background:linear-gradient(180deg,var(--sky) 0%,#8fd3f7 55%,var(--white) 100%);padding:38px 44px}
.comp-head{display:flex;align-items:center;gap:14px;color:var(--white);font-weight:700;font-size:21px;padding-bottom:12px;border-bottom:1px solid rgba(255,255,255,.8);width:280px}
.comp-upto{font-size:46px;color:var(--ink);margin:26px 0 0 145px;line-height:1}
.comp-amount{font-size:92px;font-weight:700;color:var(--ink);margin-left:145px;line-height:1}
.mri-photo{position:absolute;left:0;top:1452px;width:720px;height:245px;
  background:linear-gradient(90deg,rgba(190,200,225,.85) 0%,rgba(200,205,225,.6) 55%,rgba(255,255,255,0) 100%)}
.divider{position:absolute;left:108px;top:1497px;width:983px;height:2px;background:var(--ink)}
.contact{position:absolute;left:560px;top:1525px;width:620px;text-align:center}
.contact h2{color:var(--cyan);font-size:29px;font-weight:700}
.contact p{color:var(--ink);font-size:23px;margin-top:2px}
.contact .email{display:flex;justify-content:center;align-items:center;gap:18px;margin-top:18px;font-size:23px;color:var(--ink)}
</style>
</head>
<body>
<main class="flyer">
  <div class="hero-photo" role="img" aria-label="Photo of a young girl with her hands to her temples and a glowing brain graphic, tinted in violet and blue"></div>

  <svg class="white-base" viewBox="0 0 1200 1697" aria-hidden="true">
    <path d="M0 965 Q20 895 150 893 L1050 893 Q1180 893 1200 1010 L1200 1697 L0 1697 Z" fill="#ffffff"/>
    <path d="M0 965 Q20 895 150 893 L200 893" fill="none" stroke="#18a9ee" stroke-width="10"/>
    <path d="M1030 893 Q1180 893 1200 1010" fill="none" stroke="#18a9ee" stroke-width="10"/>
  </svg>

  <div class="brand">
    <span class="brand-dot"></span>
    <span class="brand-name">SOLVE STUDY</span>
  </div>
  <p class="brand-tagline">Sequoia Outlook Lantern Valley Echo</p>

  <h1 class="headline">
    <span class="ask">Are you the parent</span>
    <span class="ask">of a child age 10-17?</span>
    <span class="sub">Do they worry or overthink</span>
    <span class="sub">negative emotions?</span>
  </h1>
  <div class="accent-bar"></div>

  <p class="intro">Ridgeview University researchers are seeking <strong>girls age 10-17</strong> for a study about brain activity in emotions and decision-making and how they relate to puberty, anxiety and depression.</p>

  <div class="involves">
    <div class="step step-interview">
      <svg viewBox="0 0 100 90" width="100" fill="none" stroke="#1b1f4f" stroke-width="3">
        <rect x="4" y="18" width="66" height="50" rx="3"/><line x1="37" y1="68" x2="37" y2="80"/><line x1="22" y1="82" x2="52" y2="82"/>
        <circle cx="37" cy="36" r="8"/><path d="M22 62 Q37 44 52 62"/>
        <rect x="62" y="4" width="32" height="22" rx="4"/><circle cx="71" cy="15" r="1.5"/><circle cx="78" cy="15" r="1.5"/><circle cx="85" cy="15" r="1.5"/>
      </svg>
      <h3>One one-hour interview</h3>
      <p>(Online Or In-person) Where Your Child Will Discuss Their Thoughts</p>
    </div>
    <div class="step step-forms">
      <svg viewBox="0 0 70 90" width="70" fill="none" stroke="#1b1f4f" stroke-width="3">
        <rect x="6" y="10" width="58" height="76" rx="4"/><rect x="22" y="4" width="26" height="12" rx="3"/>
        <path d="M16 34l4 4 6-7M16 52l4 4 6-7M16 70l4 4 6-7"/><line x1="32" y1="36" x2="54" y2="36"/><line x1="32" y1="54" x2="54" y2="54"/><line x1="32" y1="72" x2="54" y2="72"/>
      </svg>
      <h3>Online questionnaires</h3>
      <p>(parent and child)</p>
    </div>
    <div class="step step-visit">
      <svg viewBox="0 0 100 90" width="100" fill="none" stroke="#1b1f4f" stroke-width="3">
        <path d="M30 76 V40 A34 34 0 0 1 98 40 V76 Z"/><circle cx="64" cy="44" r="16"/><circle cx="64" cy="44" r="24"/>
        <rect x="2" y="62" width="70" height="14" rx="2"/><line x1="2" y1="84" x2="98" y2="84"/>
      </svg>
      <h3>One two-hour visit</h3>
      <p>where your child will complete an MRI scan, answer questions about their puberty stage, and have a small hair sample taken to study puberty hormones</p>
    </div>
  </div>
  <div class="involves-label">Study Participation Involves:</div>

  <section class="eligible">
    <div class="eligible-head">
      <svg width="34" height="34" viewBox="0 0 34 34"><circle cx="17" cy="17" r="17" fill="#18a9ee"/><circle cx="17" cy="10" r="3.5" fill="#fff"/><path d="M12 25v-8h10v8" stroke="#fff" stroke-width="2.5" fill="none"/></svg>
      <span>Your child may<br>be eligible if they:</span>
    </div>
    <ul>
      <li><svg width="20" height="20" viewBox="0 0 20 20"><circle cx="10" cy="10" r="10" fill="#fff"/><path d="M5.5 10.5l3 3 6-6.5" stroke="#141a4a" stroke-width="2.2" fill="none"/></svg>Are age 10-17</li>
      <li><svg width="20" height="20" viewBox="0 0 20 20"><circle cx="10" cy="10" r="10" fill="#fff"/><path d="M5.5 10.5l3 3 6-6.5" stroke="#141a4a" stroke-width="2.2" fill="none"/></svg>Tend to worry or overthink negative thoughts</li>
      <li><svg width="20" height="20" viewBox="0 0 20 20"><circle cx="10" cy="10" r="10" fill="#fff"/><path d="M5.5 10.5l3 3 6-6.5" stroke="#141a4a" stroke-width="2.2" fill="none"/></svg>Have not been diagnosed with psychosis, learning problems, or autism</li>
    </ul>
  </section>

  <section class="comp">
    <div class="comp-head">
      <svg width="34" height="34" viewBox="0 0 34 34"><circle cx="17" cy="17" r="17" fill="#1b1f4f"/><rect x="9" y="14" width="16" height="12" fill="none" stroke="#fff" stroke-width="2"/><line x1="8" y1="14" x2="26" y2="14" stroke="#fff" stroke-width="2"/><line x1="17" y1="11" x2="17" y2="26" stroke="#fff" stroke-width="2"/></svg>
      <span>COMPENSATION</span>
    </div>
    <p class="comp-upto">UP TO</p>
    <p class="comp-amount">$140</p>
  </section>

  <div class="mri-photo" role="img" aria-label="Soft, faded photo of a child lying on an MRI scanner bed with headphones"></div>
  <div class="divider"></div>

  <section class="contact">
    <h2>Interested In Participating?</h2>
    <p>Want More Information? Please Contact Us!</p>
    <div class="email">
      <svg width="36" height="26" viewBox="0 0 36 26"><rect x="1" y="1" width="34" height="24" fill="#18a9ee"/><path d="M1 1l17 14L35 1" stroke="#fff" stroke-width="2" fill="none"/></svg>
      <span>solvestudy@ridgeview.edu</span>
    </div>
  </section>
</main>
</body>
</html>
```